Ashmoor Web Design Project

I need the front page and an internal page designed for this client's website. The logo is attached. Obviously the colors have to go with and/or work with the logo colors. I also attached a very rough brochure layout to help you see the direction we're going in with print materials. The rough site map is also attached. I see a slider on the homepage, the art for which I may come back to you to create. This clinic is in a very high end Dallas neighborhood. The hook is that it's a primary care and urgent facility with convenient hours.

I don't know how much this impacts your design, but this will be a Wordpress site and I'm using a framework called Brovila (brovila.com). If Brovila proves to be inflexible, I'll have to get a template that allows me to execute your design.

This site (http://lanternvaleclinic.com) has the type and quality of content I will eventually have on the Ashmoor site.

I just revised the brief for this project. I added the site map and added details to the overview and the "Must Have" section. Thank you for revisiting the brief. 

Reason: Christmas was a bad time to end it.

Target Market(s)

Women 25-54 with children living at home, income over $150k/year

Industry/Entity Type

Clinic

Requirements
Must have
• Masthead incorporating the logo
Followed by the primary nav
Slider on the home page below that
Dual nav - 1 with the nav in the attached site map
2 secondary nav with areas of healthcare
There will three blocks under the nav
1. It's about time (with a small blurb less than 50 words.
2. It's about choices (with small blurb)
3. It's about you (with small blurb)
Three footer blocks
patient check in link on every page
"No appointment? No problem" icon on every page

```html
<!DOCTYPE html>
<html lang="en">
<head>
<meta charset="utf-8">
<title>Ashmoor Medical</title>
<link href="https://fonts.googleapis.com/css2?family=Arimo:wght@400;700&display=swap" rel="stylesheet">
<style>
:root{
  --blue:#1d5fa6;
  --blue-dark:#0f4c8c;
  --green:#1aa650;
  --text:#6b6b6b;
  --link:#2a6cb0;
  --line:#dcdfe3;
  --page:#eceef1;
  --footer:#3d3d3d;
}
*{margin:0;padding:0;box-sizing:border-box}
html,body{width:952px;height:1200px;overflow:hidden}
body{position:relative;font-family:"Arimo",Arial,sans-serif;background:linear-gradient(#fff 0,#f7f8fa 150px,var(--page) 420px);color:var(--text)}
.abs{position:absolute}
ul{list-style:none}

/* top bar */
.topbar{left:0;top:0;width:952px;height:36px;border-bottom:1px solid #e3e6ea;background:linear-gradient(#f4f5f8,#fff)}
.social{top:8px;width:20px;height:20px;border-radius:50%}
.topnav{top:0;left:681px;height:36px;display:flex;font-size:9.5px;letter-spacing:.3px}
.topnav a{display:block;padding:0 14px;line-height:36px;border-left:1px solid #e0e3e7;color:#555;text-decoration:none}
.topnav a:last-child{border-right:1px solid #e0e3e7}
.topnav a.reg{color:var(--blue)}

/* masthead */
.brand{left:73px;top:55px;display:flex;align-items:center;gap:8px}
.brand-mark{width:44px;height:44px;border-radius:50%;background:var(--blue)}
.brand-name{font-size:29px;font-weight:700;color:var(--blue);letter-spacing:-.3px;line-height:1}
.brand-tag{font-size:9.5px;color:#444;margin-top:3px;padding-left:30px}
.contact{top:74px;font-size:12.5px;color:var(--blue);display:flex;align-items:center;gap:6px}
.contact b{font-weight:400;color:var(--green)}
.contact-sep{left:640px;top:75px;width:1px;height:14px;background:#ccc}

/* nav */
.nav{left:70px;top:123px;width:813px;height:46px;border-top:3px solid var(--green);background:linear-gradient(#2469b3,#1553a0);display:flex}
.nav a{display:block;color:#fff;font-size:11.5px;text-decoration:none;text-align:center;line-height:43px;border-right:1px solid #0e4485}
.nav a.on{background:var(--green)}
.hours{display:flex;align-items:center;gap:8px;padding-left:30px;color:#fff;font-size:10.5px;line-height:15px}

/* slider */
.slider{left:70px;top:173px;width:813px;height:244px;border:3px solid #4a4d52;background:linear-gradient(100deg,#cfe6f6 0%,#bcdcf2 55%,#a9d1ef 100%)}
.slider-photo{right:0;top:0;width:330px;height:238px;background:linear-gradient(90deg,rgba(190,220,242,0),#d6b89c 35%,#b8906f 70%,#c9a784)}
.slider h1{left:20px;top:60px;font-weight:400;font-size:18px;line-height:26px;color:#222}
.btn-light{left:20px;top:123px;background:#fff;border-radius:3px;color:var(--blue);font-size:10.5px;padding:5px 9px;box-shadow:0 1px 2px rgba(0,0,0,.15)}
.dots{left:23px;top:216px;display:flex;gap:9px}
.dots i{width:8px;height:8px;border-radius:50%;background:#333;border:1px solid #fff}
.dots i.on{background:var(--link)}

/* content */
.content{left:70px;top:424px;width:813px;height:408px;background:#fff}
h2.col-title{font-weight:400;color:var(--green);font-size:13px}
.para{font-size:10.4px;line-height:18.2px;text-align:justify;color:#6a6a6a}
.btn{background:linear-gradient(#3f7cc0,#23609f);color:#fff;font-size:10.5px;border-radius:3px;padding:6px 9px;box-shadow:0 1px 2px rgba(0,0,0,.25)}
.video{left:93px;top:673px;width:200px;height:114px;background:#1c2636;border:2px solid #1b1b1b}
.video-frame{left:0;top:0;width:196px;height:100px;background:linear-gradient(#8fa8c4,#6d7f94 60%,#5a6a52)}
.video-bar{left:0;bottom:0;width:196px;height:10px;background:#111}
.play{left:88px;top:39px;width:26px;height:18px;border-radius:4px;background:rgba(0,0,0,.8)}
.vdiv{left:309px;top:445px;width:1px;height:384px;background:var(--line)}
.thumb{left:745px;top:479px;width:130px;height:98px;background:linear-gradient(150deg,#eef3f8 0%,#f0cfa8 40%,#d9a14a 75%,#9fb43a);border:1px solid #e3e3e3}
.hr{height:1px;background:var(--line)}
.box{top:616px;width:262px;height:212px;border:1px solid #ececec;background:linear-gradient(#f7f7f7,#fff 40px)}
.box h3{position:absolute;left:19px;top:12px;font-weight:400;color:var(--green);font-size:13.5px}
.box ul{position:absolute;left:19px;top:40px}
.box li{font-size:10px;color:var(--link);height:23.2px;display:flex;align-items:center;gap:10px}
.box .rule{position:absolute;left:0;top:36px;width:260px;height:1px;background:#ececec}

/* book tab */
.book{left:915px;top:478px;width:37px;height:206px;background:linear-gradient(90deg,#1c5da3,#2a72bd);border-radius:4px 0 0 4px}
.book span{position:absolute;left:5px;top:160px;transform:rotate(-90deg);transform-origin:0 0;color:#fff;font-size:12.5px;font-weight:700;white-space:nowrap;letter-spacing:.3px}
.book-arrow{left:902px;top:570px}

/* service columns */
.svc{width:260px}
.svc h4{font-weight:400;color:var(--blue);font-size:11.8px;margin-bottom:10px}
.svc li{font-size:10.4px;color:#666;height:18.2px;padding-left:15px;position:relative}
.svc li::before{content:"";position:absolute;left:4px;top:5px;width:3px;height:3px;border-radius:50%;background:#aaa}

/* footer */
.footer{left:0;top:1140px;width:952px;height:60px;background:var(--footer);color:#ddd;font-size:10.4px;text-align:center}
.footer .links{margin-top:12px;word-spacing:2px}
.footer .copy{margin-top:10px}
</style>
</head>
<body>

<div class="abs topbar"></div>
<span class="abs social" style="left:588px;background:#3b5a98"></span>
<span class="abs social" style="left:616px;background:#4cb4de"></span>
<span class="abs social" style="left:644px;background:#c8312b"></span>
<nav class="abs topnav"><a class="reg">REGISTER</a><a>LOG IN</a><a>BLOG</a></nav>

<div class="abs brand">
  <span class="brand-mark"></span>
  <div>
    <div class="brand-name">AshmoorMedical</div>
    <div class="brand-tag">Immediate Family and Personal Care</div>
  </div>
</div>

<div class="abs contact" style="left:454px">
  <svg width="12" height="12" viewBox="0 0 12 12"><path d="M2 1l2 0 1 3-1.5 1a6 6 0 0 0 3 3L8 6.5l3 1v2c0 .8-.7 1.5-1.5 1.5A9 9 0 0 1 1 2.5C1 1.7 1.2 1 2 1z" fill="var(--blue)"/></svg>
  <span>Call us : (555) 204 7316</span>
</div>
<div class="abs contact-sep"></div>
<div class="abs contact" style="left:662px">
  <svg width="11" height="10" viewBox="0 0 11 10"><path d="M1 4l4.5-3 4.5 3v5H1z" fill="none" stroke="var(--blue)" stroke-width="1.2"/><path d="M1 4l4.5 3 4.5-3" fill="none" stroke="var(--blue)" stroke-width="1.2"/></svg>
  <span>E-mail : <b>info@ashmoormedical.com</b></span>
</div>

<nav class="abs nav">
  <a style="width:77px">Home</a>
  <a style="width:80px">About</a>
  <a class="on" style="width:93px">Services</a>
  <a style="width:75px">Staff</a>
  <a style="width:98px">Insurance</a>
  <a style="width:86px">Videos</a>
  <a style="width:101px">Contact us</a>
  <div class="hours">
    <svg width="22" height="22" viewBox="0 0 22 22"><circle cx="11" cy="12" r="8" fill="none" stroke="#fff" stroke-width="2"/><path d="M11 7v5l3 2" stroke="#fff" stroke-width="1.8" fill="none"/><path d="M2 5l4-3M20 5l-4-3" stroke="#fff" stroke-width="2"/></svg>
    <div>Mon.-Sat. 8am - 10pm<br>Sun. 9am - 6pm</div>
  </div>
</nav>

<section class="abs slider">
  <div class="abs slider-photo" role="img" aria-label="Smiling family of three: mother, father and daughter"></div>
  <h1 class="abs">Concierge - quality healthcare<br>for your whole family...</h1>
  <span class="abs btn-light">View more</span>
  <div class="abs dots"><i class="on"></i><i></i><i></i><i></i></div>
</section>

<div class="abs content"></div>

<h2 class="abs col-title" style="left:91px;top:447px">Videos</h2>
<p class="abs para" style="left:91px;top:475px;width:202px">Sed ut perspiciatis unde omnis iste natus error sit voluptatem accusantium dolorem-que laudantium, totam rem aperiam, eaque ipsa quae ab illo inventore veritatis et quasi architecto beatae vitae dicta sunt expli-cabo.</p>
<p class="abs para" style="left:91px;top:592px;width:202px">Nemo enim ipsam voluptatem quia volup-tas sit aspernatur aut odit aut fugit, sed quia consequuntur magni dolores eos qui ratione voluptatem sequi nesciunt.</p>
<div class="abs video">
  <div class="abs video-frame" role="img" aria-label="Video still of a smiling older couple outdoors"></div>
  <span class="abs play"><svg width="26" height="18" viewBox="0 0 26 18"><path d="M10 5l7 4-7 4z" fill="#fff"/></svg></span>
  <div class="abs video-bar"><div style="width:48px;height:2px;background:#c00;margin-top:1px"></div></div>
</div>
<span class="abs btn" style="left:92px;top:799px">View All Videos</span>

<div class="abs vdiv"></div>

<h2 class="abs col-title" style="left:323px;top:444px;font-size:16.5px">Welcome to our site</h2>
<p class="abs para" style="left:323px;top:475px;width:411px;font-size:10.8px">Ashmoor Medical Center is a full service medical facility with in-house lab and X-ray. We are here to take care of your medical needs whether they be family practice, urgent care or occupational in nature. Our providers and staff are eager to assist patients in a friendly efficient manner.</p>
<span class="abs btn" style="left:323px;top:555px">View more</span>
<div class="abs thumb" role="img" aria-label="Smiling child with a bowl of fresh fruit"></div>

<div class="abs hr" style="left:321px;top:601px;width:553px"></div>

<div class="abs box" style="left:322px">
  <h3>Family Medical Care</h3><div class="rule"></div>
  <ul>
    <li><svg width="11" height="8" viewBox="0 0 11 8"><path d="M0 2h6V0l5 4-5 4V6H0z" fill="#8fb0d6"/></svg>Cough, Colds, Flu Shots &amp; Strep Throat</li>
    <li><svg width="11" height="8" viewBox="0 0 11 8"><path d="M0 2h6V0l5 4-5 4V6H0z" fill="#8fb0d6"/></svg>Sinus &amp; Allergy Issues</li>
    <li><svg width="11" height="8" viewBox="0 0 11 8"><path d="M0 2h6V0l5 4-5 4V6H0z" fill="#8fb0d6"/></svg>Back, Chest &amp; Abdominal Pain</li>
    <li><svg width="11" height="8" viewBox="0 0 11 8"><path d="M0 2h6V0l5 4-5 4V6H0z" fill="#8fb0d6"/></svg>Wellness Exams/ Preventative Care</li>
    <li><svg width="11" height="8" viewBox="0 0 11 8"><path d="M0 2h6V0l5 4-5 4V6H0z" fill="#8fb0d6"/></svg>Pediatric Care</li>
    <li><svg width="11" height="8" viewBox="0 0 11 8"><path d="M0 2h6V0l5 4-5 4V6H0z" fill="#8fb0d6"/></svg>Men's Screening Tests</li>
    <li><svg width="11" height="8" viewBox="0 0 11 8"><path d="M0 2h6V0l5 4-5 4V6H0z" fill="#8fb0d6"/></svg>Women's Health Screenings</li>
  </ul>
</div>
<div class="abs box" style="left:612px">
  <h3>Additional Services</h3><div class="rule"></div>
  <ul>
    <li><svg width="11" height="8" viewBox="0 0 11 8"><path d="M0 2h6V0l5 4-5 4V6H0z" fill="#8fb0d6"/></svg>Travel Vaccinations/Immunizations</li>
    <li><svg width="11" height="8" viewBox="0 0 11 8"><path d="M0 2h6V0l5 4-5 4V6H0z" fill="#8fb0d6"/></svg>US Immigration (INS) Physical Exams</li>
    <li><svg width="11" height="8" viewBox="0 0 11 8"><path d="M0 2h6V0l5 4-5 4V6H0z" fill="#8fb0d6"/></svg>Occupational/Employment</li>
    <li><svg width="11" height="8" viewBox="0 0 11 8"><path d="M0 2h6V0l5 4-5 4V6H0z" fill="#8fb0d6"/></svg>Physical Exams</li>
    <li><svg width="11" height="8" viewBox="0 0 11 8"><path d="M0 2h6V0l5 4-5 4V6H0z" fill="#8fb0d6"/></svg>Drug Testing/Screening</li>
    <li><svg width="11" height="8" viewBox="0 0 11 8"><path d="M0 2h6V0l5 4-5 4V6H0z" fill="#8fb0d6"/></svg>Pregnancy, HIV &amp; STD Screening</li>
    <li><svg width="11" height="8" viewBox="0 0 11 8"><path d="M0 2h6V0l5 4-5 4V6H0z" fill="#8fb0d6"/></svg>Lacerations &amp; X-Rays</li>
  </ul>
</div>

<svg class="abs book-arrow" width="14" height="24" viewBox="0 0 14 24"><path d="M14 0v24L0 12z" fill="#2566ae"/></svg>
<div class="abs book">
  <span>BOOK APPOINTMENT</span>
  <svg class="abs" style="left:10px;top:175px" width="16" height="16" viewBox="0 0 16 16"><rect x="2" y="2" width="11" height="12" fill="#fff" stroke="#999"/><path d="M4 6h7M4 9h7M4 12h5" stroke="#999"/></svg>
</div>

<div class="abs hr" style="left:79px;top:858px;width:795px"></div>

<div class="abs svc" style="left:108px;top:876px">
  <h4>Family Medicine</h4>
  <ul><li>Cough, Colds, Flu Shots &amp; Strep Throat</li><li>Sinus, Allergy &amp; Asthma Issues</li><li>Back, chest &amp; Abdominal Pain</li><li>Rash &amp; Skin Problems</li><li>Wellness Exams/ Preventative Care</li></ul>
</div>
<div class="abs svc" style="left:382px;top:876px">
  <h4>Adult Men</h4>
  <ul><li>Cough, Colds, Flu Shots &amp; Strep Throat</li><li>Sinus, Allergy &amp; Asthma Issues</li><li>Back, chest &amp; Abdominal Pain</li><li>Rash &amp; Skin Problems</li><li>Wellness Exams/ Preventative Care</li></ul>
</div>
<div class="abs svc" style="left:647px;top:876px">
  <h4>Adult Women</h4>
  <ul><li>Cough, Colds, Flu Shots &amp; Strep Throat</li><li>Sinus, Allergy &amp; Asthma Issues</li><li>Back, chest &amp; Abdominal Pain</li><li>Rash &amp; Skin Problems</li><li>Wellness Exams/ Preventative Care</li></ul>
</div>
<div class="abs svc" style="left:108px;top:1010px">
  <h4>Kids/Teens/School</h4>
  <ul><li>Cough, Colds, Flu Shots &amp; Strep Throat</li><li>Sinus, Allergy &amp; Asthma Issues</li><li>Back, chest &amp; Abdominal Pain</li><li>Rash &amp; Skin Problems</li><li>Wellness Exams/ Preventative Care</li></ul>
</div>
<div class="abs svc" style="left:382px;top:1010px">
  <h4>Pediatric/Infant</h4>
  <ul><li>Cough, Colds, Flu Shots &amp; Strep Throat</li><li>Sinus, Allergy &amp; Asthma Issues</li><li>Back, chest &amp; Abdominal Pain</li><li>Rash &amp; Skin Problems</li><li>Wellness Exams/ Preventative Care</li></ul>
</div>
<div class="abs svc" style="left:647px;top:1010px">
  <h4>Minor Emergency</h4>
  <ul><li>Cough, Colds, Flu Shots &amp; Strep Throat</li><li>Sinus, Allergy &amp; Asthma Issues</li><li>Back, chest &amp; Abdominal Pain</li><li>Rash &amp; Skin Problems</li><li>Wellness Exams/ Preventative Care</li></ul>
</div>

<footer class="abs footer">
  <div class="links">Home &nbsp;| &nbsp;About &nbsp;| &nbsp;Services &nbsp;| &nbsp;Staff &nbsp;| &nbsp;Insurance &nbsp;| &nbsp;Videos &nbsp;| &nbsp;Contact us</div>
  <div class="copy">Copyright © &nbsp;2012 &nbsp;www.ashmoorfamilymedical.com &nbsp;&nbsp;&nbsp;&nbsp;&nbsp;All rights reserved.</div>
</footer>

</body>
</html>
```